Stationery Design Project

I need a stationary design for our company. we are based in Houston, TX and we are called Mira Vell Lending. And we are wanting to brand our MoneyMendPlus program, which includes our tax preparation and restoration, credit repair service. Although our business offers other programs, we are interested in mainly focusing on The MoneyMendPlus program. We are looking for way to brand our ourselves and I believe that a great stationery design will help in achieving this goal. Our logo design is blue and light blue. the slogan is orange.

Industry/Entity Type

Business

Requirements
Must have
• Address: 30871 Calloway Ln. B-22
Houston, TX 75419
Tel. 555-318-6207
Fax 555-294-7153
www.miravelllending.example
info@miravelllending.example
Our Slogan: Confidence, Renewed!

```html
<!DOCTYPE html>
<html lang="en">
<head>
<meta charset="utf-8">
<title>MoneyMendPlus Business Card</title>
<link rel="stylesheet" href="https://fonts.googleapis.com/css2?family=Tinos&family=Questrial&display=swap">
<style>
  :root {
    --page: #ece9e4;
    --card: #ffffff;
    --navy: #163d63;
    --blue: #1f6aa5;
    --orange: #ee8e25;
    --ink: #333333;
    --rule: #c9c9c9;
    --faint: #eef1f5;
  }
  * { margin: 0; padding: 0; box-sizing: border-box; }
  html, body { width: 1200px; height: 729px; overflow: hidden; }
  body { background: var(--page); position: relative; font-family: "Questrial", sans-serif; color: var(--ink); }

  .card {
    position: absolute;
    width: 560px;
    height: 320px;
    background: var(--card);
    box-shadow: 0 6px 18px rgba(0,0,0,0.18);
    overflow: hidden;
  }
  .card--front { left: 40px; top: 60px; }
  .card--back { left: 600px; top: 350px; }

  /* front */
  .wordmark {
    position: absolute;
    font-family: "Tinos", serif;
    color: var(--blue);
    letter-spacing: -1px;
    white-space: nowrap;
  }
  .card--front .wordmark { left: 40px; top: 112px; font-size: 50px; }
  .slogan {
    position: absolute;
    left: 60px; top: 182px;
    color: var(--orange);
    font-size: 19px;
    letter-spacing: 6px;
    white-space: nowrap;
  }
  .partner {
    position: absolute;
    right: 28px; top: 34px;
    display: flex; align-items: center; gap: 10px;
  }
  .partner__square { width: 22px; height: 22px; background: var(--navy); }
  .partner__name { font-family: "Tinos", serif; font-size: 16px; color: var(--navy); }

  .address {
    position: absolute;
    left: 60px; top: 248px;
    width: 210px;
    text-align: right;
    font-size: 14px;
    line-height: 20px;
    font-style: normal;
  }
  .divider {
    position: absolute;
    left: 286px; top: 224px;
    width: 1px; height: 80px;
    background: var(--rule);
  }
  .contact {
    position: absolute;
    left: 298px; top: 226px;
    list-style: none;
    font-size: 13.5px;
    line-height: 19px;
  }
  .contact li { display: flex; align-items: center; gap: 6px; white-space: nowrap; }
  .contact svg { width: 11px; height: 11px; fill: var(--blue); flex: none; }

  /* back */
  .back__panel {
    position: absolute;
    left: 150px; top: 30px;
    width: 260px; height: 240px;
    background: var(--faint);
  }
  .card--back .wordmark { left: 0; right: 0; top: 118px; text-align: center; font-size: 66px; }
  .back__url {
    position: absolute;
    left: 0; right: 0; top: 232px;
    text-align: center;
    font-family: "Tinos", serif;
    font-size: 15px;
    letter-spacing: 5px;
    color: var(--navy);
    white-space: nowrap;
  }
</style>
</head>
<body>

<section class="card card--front" aria-label="Business card front">
  <div class="partner">
    <span class="partner__square"></span>
    <span class="partner__name">Mira Vell Lending</span>
  </div>
  <div class="wordmark">MoneyMendPlus</div>
  <div class="slogan">Confidence, Renewed!</div>

  <address class="address">
    30871 Calloway Ln. B-22<br>Houston<br>TX 75419
  </address>
  <div class="divider"></div>
  <ul class="contact">
    <li><svg viewBox="0 0 12 12"><path d="M2.5 1 L4.5 1 L5.3 3.6 L4 4.6 C4.6 6 5.9 7.4 7.4 8 L8.4 6.7 L11 7.5 L11 9.5 C11 10.3 10.3 11 9.5 11 C5 11 1 7 1 2.5 C1 1.7 1.7 1 2.5 1Z"/></svg>555-318-6207</li>
    <li><svg viewBox="0 0 12 12"><path d="M3 1h5v3H3z M1 5h10v5H1z M3 7h6v1H3z"/></svg>555-294-7153</li>
    <li><svg viewBox="0 0 12 12"><path d="M1 2.5h10v7H1z" fill="none" stroke="#1f6aa5" stroke-width="1.2"/><path d="M1 2.5 L6 6.5 L11 2.5" fill="none" stroke="#1f6aa5" stroke-width="1.2"/></svg>info@miravelllending.example</li>
    <li><svg viewBox="0 0 12 12"><circle cx="6" cy="6" r="5" fill="none" stroke="#1f6aa5" stroke-width="1.1"/><path d="M1 6h10 M6 1c-2.5 3-2.5 7 0 10 M6 1c2.5 3 2.5 7 0 10" fill="none" stroke="#1f6aa5" stroke-width="0.9"/></svg>www.miravelllending.example</li>
  </ul>
</section>

<section class="card card--back" aria-label="Business card back">
  <div class="back__panel"></div>
  <div class="wordmark">MoneyMendPlus</div>
  <div class="back__url">www.miravelllending.example</div>
</section>

</body>
</html>
```